VFX Company Business Card Design Project

The Kestrel Works is a decentralized Visual Effects Studio servicing the television and feature film industries.
Project Brief:
Take our logo that was previously designed on Pencil Harbor and make a double sided business card.
Requirements:
- Card MUST be double sided.
- Front of card MUST have the yellow part of our logo against the dark grey background.
- Back of card is completely up to the designer.
- Back of card must include the complete company logo.
Please follow these File Preparation guidelines:
http://printnook.ca/infopage?file=filetype_en&s=PrintNook_new&lang=en
Business

```html
<!DOCTYPE html>
<html lang="en">
<head>
<meta charset="utf-8">
<title>The Kestrel Works – Business Card</title>
<link rel="stylesheet" href="https://fonts.googleapis.com/css2?family=Questrial&family=PT+Sans&display=swap">
<style>
  :root {
    --backdrop: #c89c74;
    --card: #2b2b2b;
    --band: #5e6a6a;
    --accent: #f7c326;
    --light: #e4e6e1;
    --white: #ffffff;
    --label: #1e1e1e;
    --shadow: rgba(40, 20, 5, 0.45);
  }
  * { margin: 0; padding: 0; box-sizing: border-box; }
  html, body { width: 1200px; height: 788px; overflow: hidden; }
  body {
    position: relative;
    background: var(--backdrop);
    font-family: "PT Sans", Arial, sans-serif;
  }
  .side-label {
    position: absolute;
    font-family: "PT Sans", Arial, sans-serif;
    font-size: 22px;
    color: var(--label);
    transform: translateX(-50%);
    white-space: nowrap;
  }
  .card {
    position: absolute;
    width: 525px;
    height: 300px;
    background: var(--card);
    border-radius: 20px;
    box-shadow: 2px 4px 8px var(--shadow);
    overflow: hidden;
  }
  .card--back { left: 338px; top: 74px; }
  .card--front-mark { left: 54px; top: 445px; }
  .card--front-full { left: 622px; top: 445px; }

  .wordmark {
    position: absolute;
    font-family: "Questrial", Arial, sans-serif;
    white-space: nowrap;
  }
  .card--back .wordmark {
    left: 88px; top: 58px;
    font-size: 40px;
    color: var(--light);
    letter-spacing: 0.5px;
  }
  .name-band {
    position: absolute;
    left: 0; top: 153px;
    width: 450px; height: 34px;
    background: var(--band);
    font-family: "Questrial", Arial, sans-serif;
    color: var(--white);
    padding-left: 121px;
    line-height: 34px;
    font-size: 19px;
  }
  .name-band .designation { font-size: 14px; }
  .band-tab {
    position: absolute;
    left: 458px; top: 153px;
    width: 67px; height: 34px;
    background: var(--white);
  }
  .contact-list {
    position: absolute;
    left: 77px; top: 211px;
    list-style: none;
    font-size: 12.5px;
    color: var(--white);
  }
  .contact-list li {
    display: flex; align-items: center;
    height: 20px;
  }
  .contact-list svg { width: 11px; height: 11px; margin-right: 5px; fill: var(--band); }
  .address {
    position: absolute;
    left: 242px; top: 237px;
    font-size: 12.5px;
    line-height: 17px;
    color: var(--white);
    font-style: normal;
  }

  .card--front-mark .wordmark {
    left: 0; right: 0; top: 106px;
    text-align: center;
    font-size: 50px;
    color: var(--accent);
  }
  .card--front-full .wordmark {
    left: 0; right: 0; top: 124px;
    text-align: center;
    font-size: 40px;
    color: var(--accent);
  }
  .site {
    position: absolute;
    left: 0; right: 0; top: 257px;
    text-align: center;
    font-family: "PT Sans", Arial, sans-serif;
    font-size: 21px;
    letter-spacing: 3.5px;
    color: var(--white);
  }
</style>
</head>
<body>
  <div class="side-label" style="left:600px; top:32px;">Back</div>
  <div class="side-label" style="left:327px; top:404px;">Front - 1</div>
  <div class="side-label" style="left:900px; top:404px;">Front - 2</div>

  <section class="card card--back" aria-label="Card back">
    <div class="wordmark">The Kestrel Works</div>
    <div class="name-band">Your Name, <span class="designation">Designation</span></div>
    <div class="band-tab"></div>
    <ul class="contact-list">
      <li><svg viewBox="0 0 12 12"><path d="M3 1l2 2-1 1.5c.8 1.6 2 2.8 3.5 3.5L9 7l2 2-1.5 2C5 10.5 1.5 7 1 2.5z"/></svg>123-456-7890</li>
      <li><svg viewBox="0 0 12 12"><rect x="3" y="0.5" width="6" height="11" rx="1"/></svg>123-456-7890</li>
      <li><svg viewBox="0 0 12 12"><rect x="0.5" y="2.5" width="11" height="7" rx="1"/></svg>info@website.com</li>
      <li><svg viewBox="0 0 12 12"><circle cx="6" cy="6" r="5.5"/></svg>www.website.com</li>
    </ul>
    <address class="address">0000#, Area Name<br>Street Name, State Name<br>Country code.</address>
  </section>

  <section class="card card--front-mark" aria-label="Card front, version one">
    <div class="wordmark">The Kestrel Works</div>
    <div class="site">www.website.com</div>
  </section>

  <section class="card card--front-full" aria-label="Card front, version two">
    <div class="wordmark">The Kestrel Works</div>
    <div class="site">www.website.com</div>
  </section>
</body>
</html>
```